Upmarket Dessert Lounge needs a Business Card Design

We are an upmarket dessert lounge needing a business card to match our image.

We want something that is simple yet beautiful, feminine, classy, sophisticated and elegant. We want it to stand out and don't mind if it is bold.

The design should include our logo and colours of red or maroon with gold highlights. We don't mind if black is used.

Marlow & Quince

Target Market(s)

For those who like to indulge or treat themselves and give in to their temptations on good quality desserts.

Industry/Entity Type

Business

Requirements
Must have
• Must include our logo and our name

Marlow & Quince

M & Q

```html
<!DOCTYPE html>
<html lang="en">
<head>
<meta charset="utf-8">
<title>Marlow &amp; Quince – Business Card</title>
<link href="https://fonts.googleapis.com/css2?family=Tinos:wght@400;700&display=swap" rel="stylesheet">
<style>
  :root {
    --maroon: #7a1518;
    --gold: #f0cf9b;
    --card: #ffffff;
    --ink: #555555;
    --stage: #e8e1d9;
  }
  * { margin: 0; padding: 0; box-sizing: border-box; }
  html, body { width: 1200px; height: 417px; overflow: hidden; }
  body {
    background: var(--stage);
    position: relative;
    font-family: "Tinos", "Times New Roman", serif;
  }
  .card {
    position: absolute;
    top: 62px;
    width: 515px;
    height: 293px;
    background: var(--card);
    border-radius: 14px;
    overflow: hidden;
    box-shadow: 0 2px 6px rgba(0,0,0,0.18);
  }
  .card--front { left: 55px; }
  .card--back { left: 631px; }

  .brand-name {
    position: absolute;
    transform: translate(-50%, -50%);
    white-space: nowrap;
    color: var(--maroon);
    font-weight: 400;
    font-size: 34px;
    letter-spacing: 0.5px;
    text-transform: uppercase;
  }
  .card--front .brand-name { left: 244px; top: 97px; }
  .card--back .brand-name { left: 258px; top: 131px; }

  .gold-rule {
    position: absolute;
    left: 0; right: 0;
    top: 258px;
    height: 3px;
    background: var(--gold);
  }
  .footer-band {
    position: absolute;
    left: 0; right: 0;
    top: 264px;
    height: 29px;
    background: var(--maroon);
    color: #fff;
    font-size: 14px;
    display: flex;
    align-items: center;
    justify-content: center;
  }
  .footer-band--web { letter-spacing: 3px; font-size: 13px; }

  .person {
    position: absolute;
    left: 45px;
    top: 212px;
  }
  .person__name {
    color: var(--maroon);
    font-weight: 700;
    font-size: 17px;
    letter-spacing: 0.3px;
  }
  .person__title {
    color: var(--ink);
    font-size: 13px;
    margin-top: 1px;
  }

  .contact {
    position: absolute;
    top: 213px;
    list-style: none;
    color: var(--ink);
    font-size: 13px;
    line-height: 21px;
  }
  .contact--phones { left: 200px; }
  .contact--online { left: 335px; }
  .contact li { display: flex; align-items: center; gap: 4px; }
  .contact svg { width: 9px; height: 9px; fill: var(--ink); flex: none; }
</style>
</head>
<body>

  <section class="card card--front" aria-label="Card front">
    <div class="brand-name">Marlow &amp; Quince</div>

    <div class="person">
      <div class="person__name">YOUR NAME</div>
      <div class="person__title">Title</div>
    </div>

    <ul class="contact contact--phones">
      <li>
        <svg viewBox="0 0 10 10" aria-hidden="true"><path d="M2 0.5 L3.6 2.6 L2.8 3.6 Q4 6 6.4 7.2 L7.4 6.4 L9.5 8 L8.3 9.5 Q1 8 0.5 1.7 Z"/></svg>
        +2348120004417
      </li>
      <li>
        <svg viewBox="0 0 10 10" aria-hidden="true"><path d="M2.5 0 H7.5 V10 H2.5 Z M3.4 1.2 V7.5 H6.6 V1.2 Z"/></svg>
        +2348120004417
      </li>
    </ul>

    <ul class="contact contact--online">
      <li>
        <svg viewBox="0 0 10 10" aria-hidden="true"><path d="M0 2 H10 V8.5 H0 Z M0.8 2.6 L5 5.6 L9.2 2.6 Z" fill-rule="evenodd"/></svg>
        info@marlowquince.com
      </li>
      <li>
        <svg viewBox="0 0 10 10" aria-hidden="true"><circle cx="5" cy="5" r="4.5"/></svg>
        www.marlowquince.com
      </li>
    </ul>

    <div class="gold-rule"></div>
    <div class="footer-band">00, Complex name, City, State 0025</div>
  </section>

  <section class="card card--back" aria-label="Card back">
    <div class="brand-name">Marlow &amp; Quince</div>
    <div class="gold-rule"></div>
    <div class="footer-band footer-band--web">www.marlowquince.com</div>
  </section>

</body>
</html>
```